Customer Value Leaflet

We need a bi-fold brochure designing, based on the attached PDF wireframes. Our company name is brambleharvik.com (of which the logo is currently being designed). The corporate colour is orange (the exact shade of which we are happy to leave to the designers discretion).

The leaflet will distributed to customer experience experts and marketers so the design needs to be bright, engaging, clean and simple. Design is critical.

It Company

```html
<!DOCTYPE html>
<html lang="en">
<head>
<meta charset="utf-8">
<title>Customer Value Leaflet – Meet Kim and Kevin</title>
<link rel="stylesheet" href="https://fonts.googleapis.com/css2?family=Open+Sans:wght@300;400;600;700&display=swap">
<style>
  :root {
    --orange: #f9a637;
    --paper: #f8f8f8;
    --ink: #4a4a4a;
    --ink-dark: #2e2e2e;
    --white: #ffffff;
    --placeholder: #e4ebdf;
  }
  * { margin: 0; padding: 0; box-sizing: border-box; }
  html, body { width: 1200px; height: 1200px; overflow: hidden; }
  body {
    font-family: "Open Sans", Arial, sans-serif;
    background: var(--white);
  }
  .panel {
    position: relative;
    width: 1200px;
    height: 1200px;
    background: var(--paper);
  }
  .name-tag {
    position: absolute;
    top: 62px;
    width: 475px;
    height: 87px;
    background: var(--orange);
    color: var(--white);
    font-weight: 600;
    font-size: 39px;
    letter-spacing: 0.5px;
    display: flex;
    align-items: center;
    justify-content: center;
  }
  .name-tag--kim { left: 113px; }
  .name-tag--kevin { left: 603px; }
  .character {
    position: absolute;
    background: var(--placeholder);
    border-radius: 12px;
  }
  .character--kim { left: 290px; top: 172px; width: 120px; height: 320px; }
  .character--kevin { left: 778px; top: 192px; width: 134px; height: 300px; }
  .profile {
    position: absolute;
    top: 541px;
    width: 480px;
    text-align: center;
    font-weight: 300;
    font-size: 40px;
    line-height: 48.5px;
    color: var(--ink);
  }
  .profile--kim { left: 110px; }
  .profile--kevin { left: 610px; }
  .teaser-band {
    position: absolute;
    left: 0;
    top: 1005px;
    width: 1200px;
    height: 170px;
    background: var(--orange);
    display: flex;
    align-items: center;
    justify-content: center;
    font-size: 40px;
    font-weight: 400;
    color: var(--ink-dark);
  }
</style>
</head>
<body>
  <main class="panel">
    <div class="name-tag name-tag--kim">MEET KIM</div>
    <div class="name-tag name-tag--kevin">MEET KEVIN</div>

    <div class="character character--kim" role="img" aria-label="Illustration of Kim, a smiling woman with a hair bun in a green cardigan and yellow top"></div>
    <div class="character character--kevin" role="img" aria-label="Illustration of Kevin, a smiling man with dark hair in a green jumper"></div>

    <p class="profile profile--kim">Kim has purcased<br>3 items from you over<br>the past 3 months @<br>£109 margin and you<br>acquired her though a<br>Searchly PPC campaign</p>

    <p class="profile profile--kevin">Kevin purchased<br>an item last week @<br>£31 margin and you<br>acquired him though a<br>retargeting campaign</p>

    <div class="teaser-band">Right now you probably think Kim is your best customer...</div>
  </main>
</body>
</html>
```